Commercial and Residential Paint Contractor needs website

We need a website for our residential painting, multi-family painting and commercial painting company. We paint interior and exterior of houses, apartments and commercial buildings. I would like an about us page, residential page, multi family page, commercial page and contact us. Need keywords added to website for seo opitimazation. I like this website https://www.wallcraftcrew.com/

Target Market(s)

General Contractors and commercial property managers

Coding

Coded - Design and coding required

Number of Pages Required

5+ page

Font styles to use
Sans Serif

Requirements
Must have
• I need SEO keywords on pages

```html
<!DOCTYPE html>
<html lang="en">
<head>
<meta charset="utf-8">
<title>Hartwell Painting – Commercial, Residential &amp; Multi-Family Painting</title>
<link href="https://fonts.googleapis.com/css2?family=Poppins:wght@400;500;600;700&display=swap" rel="stylesheet">
<style>
:root{
  --navy:#1d4a8c;
  --navy-dark:#163b73;
  --red:#d3202f;
  --ink:#111;
  --text:#333;
  --white:#fff;
  --dark:#2f3033;
  --sky:#7aa6dd;
  --pink:#f06a85;
}
*{box-sizing:border-box;margin:0;padding:0}
html,body{width:1200px;height:3088px;overflow:hidden}
body{position:relative;font-family:'Poppins',sans-serif;color:var(--text);background:var(--white)}
.abs{position:absolute}
.topbar{left:0;top:0;width:1200px;height:35px;background:var(--navy);color:var(--white);font-size:14px}
.topbar .welcome{left:120px;top:8px}
.topbar .mail{left:726px;top:8px;display:flex;gap:8px;align-items:center}
.topbar .phone{left:952px;top:8px;display:flex;gap:8px;align-items:center}
.header{left:0;top:35px;width:1200px;height:117px;background:var(--white)}
.brand{left:118px;top:32px;display:flex;align-items:center;gap:10px;font-size:34px;font-weight:700;color:var(--navy);letter-spacing:1px}
.brand .mark{width:18px;height:18px;background:var(--red)}
.nav{left:454px;top:54px;display:flex;gap:27px;font-size:14.5px;font-weight:500;color:var(--ink)}
.nav .active{color:var(--navy);border-bottom:2px solid var(--red);padding-bottom:8px}
.quote{left:918px;top:40px;width:164px;height:46px;background:var(--red);color:var(--white);font-size:14.5px;font-weight:600;display:flex;align-items:center;justify-content:center;transform:skewX(-8deg)}
.quote span{transform:skewX(8deg)}
.hero{left:0;top:152px;width:1200px;height:438px;background:linear-gradient(100deg,#f24a5a 0%,#ee3e4f 48%,#d42a35 62%,#e8e2e2 82%,#f4f1f0 100%)}
.hero h2{left:120px;top:156px;color:var(--white);font-size:28px;font-weight:600;letter-spacing:1px}
.hero h1{left:120px;top:205px;color:var(--white);font-size:46px;font-weight:700;letter-spacing:1.5px}
.hero svg{left:0;bottom:0}
.dots{left:994px;top:561px;display:flex;gap:10px}
.dots i{display:block;width:13px;height:13px;border-radius:50%;background:var(--white)}
.dots i.on{background:none;border:2px solid var(--white);width:17px;height:17px;margin-top:-2px}
.section-title{left:0;width:1200px;text-align:center;font-size:31px;font-weight:700;color:var(--ink);letter-spacing:.5px}
.splash{border-radius:48% 52% 44% 56%/55% 45% 55% 45%}
.worker{left:0;top:745px;width:525px;height:387px;background:linear-gradient(180deg,#f2f0ea,#e8ecef)}
.about-text{left:544px;top:762px;width:532px;font-size:15px;line-height:25.3px;text-align:justify;color:var(--text)}
.learn{left:552px;top:1000px;width:248px;height:50px;background:var(--red);color:var(--white);font-size:17px;font-weight:500;display:flex;align-items:center;justify-content:center;transform:skewX(-6deg)}
.learn span{transform:skewX(6deg)}
.services{left:0;top:1132px;width:1200px;height:696px;background:linear-gradient(135deg,#3a3a3c,#2a2b2e 60%,#3b3c40)}
.services .section-title{color:var(--white);top:100px}
.card{width:306px;height:319px}
.card-label{color:var(--white);font-size:20px;font-weight:600;white-space:nowrap}
.card-label b{font-size:36px;font-weight:600;margin-right:6px}
.photo{background:linear-gradient(160deg,#9aa7b4,#6a7a6c)}
.footer{left:0;top:2724px;width:1200px;height:364px}
.foot-h{color:var(--white);font-size:17px;font-weight:600}
.foot-h::after{content:"";display:block;width:38px;height:2px;background:var(--red);margin-top:12px}
.foot-list{color:var(--white);font-size:14px;line-height:24px;list-style:none}
.social{left:210px;top:2817px;display:flex;gap:13px}
.social i{display:block;width:32px;height:32px;border-radius:50%;background:var(--red)}
.news-input{left:580px;top:2880px;width:232px;height:42px;background:var(--navy-dark);border:1px solid #2f63ad;color:var(--white);font-size:14px;padding:12px 14px}
.news-btn{left:776px;top:2880px;width:36px;height:42px;background:var(--red);display:flex;align-items:center;justify-content:center}
.contact-row{left:868px;display:flex;gap:14px;color:var(--white);font-size:14px;line-height:28px}
.ic{width:26px;height:26px;border-radius:50%;background:var(--red);flex:none;display:flex;align-items:center;justify-content:center;margin-top:1px}
.copy{left:477px;top:3034px;color:var(--white);font-size:14px}
</style>
</head>
<body>

<div class="topbar abs">
  <div class="welcome abs">Welcome to Hartwell Painting !</div>
  <div class="mail abs"><svg width="14" height="11" viewBox="0 0 14 11"><rect width="14" height="11" rx="1" fill="#fff"/><path d="M0 1l7 5 7-5" stroke="#1d4a8c" stroke-width="1.4" fill="none"/></svg>info@hartwellpainting.com</div>
  <div class="phone abs"><svg width="14" height="14" viewBox="0 0 14 14"><rect width="14" height="14" rx="2" fill="#fff"/><path d="M4 3c0 4 3 7 7 7l0-2-2-1-1 1c-1-.5-2-1.5-2.5-2.5l1-1-1-2z" fill="#1d4a8c"/></svg>+1 555 014 2230</div>
</div>

<header class="header abs">
  <div class="brand abs"><span class="mark"></span>HARTWELL</div>
  <nav class="nav abs">
    <span class="active">HOME</span><span>ABOUT</span><span>SERVICES</span><span>PROJECT</span><span>CONTACT US</span>
  </nav>
  <div class="quote abs"><span>GET A QUOTE</span></div>
</header>

<section class="hero abs" role="img" aria-label="Hand rolling red paint onto a wall with a paint roller">
  <h2 class="abs">WE ARE EXPERT IN</h2>
  <h1 class="abs">COMMERCIAL PAINTING</h1>
  <svg class="abs" width="1200" height="44" viewBox="0 0 1200 44"><polygon points="0,44 1200,0 1200,44" fill="#1d4a8c"/></svg>
  <div class="dots abs"><i class="on"></i><i></i><i></i><i></i></div>
</section>

<div class="abs splash" style="left:552px;top:636px;width:118px;height:100px;background:var(--sky)"></div>
<h2 class="section-title abs" style="top:672px">WELCOME TO HARTWELL PAINTING</h2>
<div class="worker abs" role="img" aria-label="Smiling painter in white overalls leaning on a ladder, holding a roller and paint bucket"></div>
<p class="about-text abs">We are family owned and operated with over 10 years' experience. We pride our self in performing to the highest degree of workmanship standards. Hartwell Painting is your best choice for commercial, residential and multi-family painting in the DFW/Forth Worth area. Our experienced estimators will meet with you and customize a proposal to meet your needs. They will stay with you from the beginning of the project to the end, making sure you are 100% satisfied. If you are looking for a dependable painter call our office 555-014-7781.</p>
<div class="learn abs"><span>LEARN MORE</span></div>

<section class="services abs" role="img" aria-label="Darkened photo of a painter at work on a site">
  <div class="abs splash" style="left:555px;top:80px;width:90px;height:90px;background:var(--pink)"></div>
  <h2 class="section-title abs">OUR SERVICES</h2>
  <div class="card photo abs" style="left:118px;top:176px;background:linear-gradient(135deg,#f4f4f4 45%,#b9a89a 55%,#6a7d8f)" role="img" aria-label="House sketch blending into a painter painting the exterior"></div>
  <div class="card-label abs" style="left:137px;top:508px"><b>01.</b>Residential Painting</div>
  <div class="card photo abs" style="left:447px;top:238px;background:linear-gradient(150deg,#c9dde8,#4e6a74 55%,#d24a3c 70%,#556b6b)" role="img" aria-label="Colourful commercial library interior with red booths"></div>
  <div class="card-label abs" style="left:458px;top:570px"><b>02.</b>commercial Painting</div>
  <div class="card photo abs" style="left:777px;top:176px;background:linear-gradient(170deg,#8aa0a8,#c7b89a 40%,#5a8a4a 80%)" role="img" aria-label="Aerial view of multi-family apartment buildings"></div>
  <div class="card-label abs" style="left:785px;top:508px"><b>03.</b>Multi-family painting</div>
</section>

<div class="abs splash" style="left:553px;top:1872px;width:100px;height:105px;background:#55aee6"></div>
<h2 class="section-title abs" style="top:1912px">PROJECT GALLERY</h2>
<div class="photo abs" style="left:121px;top:2025px;width:621px;height:335px;background:linear-gradient(180deg,#2f6fd0,#6ea2e0 45%,#8a7462 65%,#b9b5ad)" role="img" aria-label="Newly painted single-storey commercial building"></div>
<div class="photo abs" style="left:753px;top:2025px;width:330px;height:335px;background:linear-gradient(180deg,#e6e6e4,#cfcfcd 60%,#8c7a68)" role="img" aria-label="White kitchen with dark island countertop"></div>
<div class="photo abs" style="left:120px;top:2370px;width:284px;height:267px;background:linear-gradient(180deg,#2a2a2a,#606066 50%,#9a9a9a)" role="img" aria-label="Gym interior with graphic wall mural"></div>
<div class="photo abs" style="left:415px;top:2370px;width:410px;height:267px;background:linear-gradient(90deg,#8a8f94,#7b6248 35%,#5a4636 70%,#8a7560)" role="img" aria-label="Reclaimed wood feature wall with gym signage"></div>
<div class="photo abs" style="left:835px;top:2370px;width:248px;height:267px;background:linear-gradient(180deg,#eaeaea,#c8c8c8 70%,#6b6b6b)" role="img" aria-label="Bright living room with tall windows"></div>

<footer class="footer abs">
  <svg class="abs" style="left:0;top:0" width="1200" height="364" viewBox="0 0 1200 364"><polygon points="250,0 1200,0 1200,364 0,364 0,70" fill="#1d4a8c"/></svg>
  <div class="abs" style="left:0;top:10px;width:440px;height:354px;background:linear-gradient(160deg,rgba(255,255,255,.18),rgba(255,255,255,.05))" role="img" aria-label="Illustration of painters rolling paint and opening paint cans"></div>
</footer>
<div class="social abs" aria-label="Social media links"><i></i><i></i><i></i></div>

<div class="abs" style="left:383px;top:2763px">
  <div class="foot-h">Quick Links</div>
  <ul class="foot-list" style="margin-top:16px"><li>Home</li><li>About US</li><li>Services</li><li>Project Gallery</li><li>Contact Us</li></ul>
</div>
<div class="abs" style="left:578px;top:2763px">
  <div class="foot-h">Newsletter</div>
  <p class="foot-list" style="margin-top:16px">Stay tune with our latest<br>updates and offers.</p>
</div>
<div class="news-input abs">Email Address</div>
<div class="news-btn abs"><svg width="10" height="16" viewBox="0 0 10 16"><path d="M2 2l6 6-6 6" stroke="#fff" stroke-width="2" fill="none"/></svg></div>
<div class="abs" style="left:875px;top:2763px"><div class="foot-h">Contact Us</div></div>
<div class="contact-row abs" style="top:2812px"><span class="ic"><svg width="10" height="14" viewBox="0 0 10 14"><path d="M5 0a5 5 0 0 1 5 5c0 4-5 9-5 9S0 9 0 5a5 5 0 0 1 5-5z" fill="#fff"/><circle cx="5" cy="5" r="2" fill="#d3202f"/></svg></span><span>4120 Larkspur Ave.,<br>Suite 210 Meadowvale,<br>CA 90000</span></div>
<div class="contact-row abs" style="top:2907px"><span class="ic"><svg width="12" height="12" viewBox="0 0 12 12"><path d="M2 1c0 5 4 9 9 9l0-2-2.5-1-1 1c-1.3-.6-2.6-1.9-3.2-3.2l1-1L4.2 1z" fill="#fff"/></svg></span><span>+1 555 014 2230</span></div>
<div class="contact-row abs" style="top:2947px"><span class="ic"><svg width="12" height="10" viewBox="0 0 12 10"><rect width="12" height="10" rx="1" fill="#fff"/><path d="M0 1l6 4 6-4" stroke="#d3202f" stroke-width="1.3" fill="none"/></svg></span><span>info@hartwellpainting.com</span></div>
<div class="copy abs">hartwellpainting@2020. All Rights Reserved.</div>

</body>
</html>
```